Dental Practice Billboard Design

We are a newer dental practice in need of a simple but appealing billboard for our growing dental practice to attract new patients. The practice is owned by husband and wife dentists and is family friendly in a small town in Kentucky. We try to be very friendly and caring to our patients. Would prefer a blue background for the billboard and our tooth logo to be prominent. We are partial to the Patua One font used in the image below but please feel free to tweak it as you deem necessary. The shape of the uppercase D and lowercase g are why we like that font, so fonts with a similarly shaped “D” and “g” would work as well. Please include our phone number (555) 847-1390. Please see our website Harlowbrookdentistry.example for more info on the practice if needed. Thank you! Looking forward to seeing your creation.
Updates

The dimensions will be 12ft x 24ft (3.6576m x 7.3152m). Apologies for not including this in the original prompt. Thank you all for your submissions.

Industry/Entity Type

Dental

Font styles to use
Other font styles liked:
• Patua One

Colors
0054AA
0677BA
7BADD7
CADEEF
E8F1F8
0094D4
00A9DD
6FCCEA
C7EBF8
E9F6FB
00AB8E
00BBA5
67D7C9
C6EFE9
E9F9F6
59FF00
82FF00
B8FF75
E3FFCB
F4FFEA

Requirements
Must have
• Phone number, website, Logo, Practice name “Harlow Brook Dentistry”
Should not have
• A tagline or slogan

```html
<!DOCTYPE html>
<html lang="en">
<head>
<meta charset="utf-8">
<title>Harlow Brook Dentistry — Billboard</title>
<link href="https://fonts.googleapis.com/css2?family=Patua+One&family=Fira+Sans:wght@600&display=swap" rel="stylesheet">
<style>
  :root {
    --navy: #022a5e;
    --green: #14b11a;
    --white: #ffffff;
    --ink: #2b2b2b;
    --page: #ffffff;
  }
  html, body {
    margin: 0;
    padding: 0;
    width: 1071px;
    height: 1200px;
    overflow: hidden;
    background: var(--page);
  }
  .billboard {
    position: absolute;
    left: 36px;
    top: 350px;
    width: 1000px;
    height: 500px;
    background: var(--navy);
    overflow: hidden;
  }
  .brand-mark {
    position: absolute;
    left: 80px;
    top: 70px;
    width: 250px;
    height: 250px;
    border-radius: 50%;
    background: var(--green);
  }
  .practice-name {
    position: absolute;
    left: 370px;
    top: 78px;
    margin: 0;
    font-family: "Patua One", Georgia, serif;
    font-weight: 400;
    color: var(--white);
    line-height: 1;
  }
  .practice-name .name-main {
    display: block;
    font-size: 92px;
    letter-spacing: 0.5px;
  }
  .practice-name .name-sub {
    display: block;
    margin-top: 34px;
    font-size: 62px;
  }
  .contact-web {
    position: absolute;
    left: 0;
    bottom: 0;
    width: 605px;
    height: 76px;
    background: var(--green);
    clip-path: polygon(0 0, 572px 0, 605px 76px, 0 76px);
    display: flex;
    align-items: center;
    padding-left: 32px;
    box-sizing: border-box;
    gap: 14px;
  }
  .contact-web .label {
    font-family: "Patua One", Georgia, serif;
    font-size: 28px;
    color: var(--white);
  }
  .contact-phone {
    position: absolute;
    right: 2px;
    bottom: 0;
    width: 414px;
    height: 62px;
    background: var(--white);
    clip-path: polygon(0 0, 414px 0, 414px 62px, 18px 62px);
    display: flex;
    align-items: center;
    padding-left: 44px;
    box-sizing: border-box;
    gap: 18px;
  }
  .contact-phone .label {
    font-family: "Fira Sans", Arial, sans-serif;
    font-weight: 600;
    font-size: 34px;
    color: var(--ink);
  }
  .icon { flex: none; }
</style>
</head>
<body>
  <section class="billboard" aria-label="Harlow Brook Dentistry billboard">
    <div class="brand-mark" aria-hidden="true"></div>

    <h1 class="practice-name">
      <span class="name-main">Harlow Brook</span>
      <span class="name-sub">Dentistry</span>
    </h1>

    <div class="contact-web">
      <svg class="icon" width="40" height="40" viewBox="0 0 40 40" aria-hidden="true">
        <circle cx="20" cy="20" r="17" fill="none" stroke="var(--white)" stroke-width="3"/>
        <ellipse cx="20" cy="20" rx="7" ry="17" fill="none" stroke="var(--white)" stroke-width="2.5"/>
        <line x1="3" y1="20" x2="37" y2="20" stroke="var(--white)" stroke-width="2.5"/>
      </svg>
      <span class="label">Harlowbrookdentistry.example</span>
    </div>

    <div class="contact-phone">
      <svg class="icon" width="44" height="44" viewBox="0 0 44 44" aria-hidden="true">
        <path d="M10 6 L17 6 L20 14 L15 18 C17 24 21 28 27 30 L31 25 L39 28 L39 35 C39 38 36 40 33 39 C19 36 9 26 6 12 C5 9 7 6 10 6 Z" fill="var(--green)"/>
        <path d="M25 8 A12 12 0 0 1 37 20" fill="none" stroke="var(--green)" stroke-width="3" stroke-linecap="round"/>
        <path d="M25 14 A6 6 0 0 1 31 20" fill="none" stroke="var(--green)" stroke-width="3" stroke-linecap="round"/>
      </svg>
      <span class="label">(555) 847-1390</span>
    </div>
  </section>
</body>
</html>
```